Road Construction Company needs business cards

We would like a new business card designed for our business.

We're a road construction company based in Qld, Australia.

Can the business card please have the following information on it.

Name: Warren Halbeck
Position: General Manager
Phone: 0472 915 348
Email: Warren.halbeck@tovrin.com.au
Address: 87 Marrow Ave, Pendlebay, QLD, 4023
Website: www.tovrin.com.au

Visually we'd like the card to be professional and simple.

Attached is our logo.

Our website is www.tovrin.com.au

Target Market(s)

Men aged 25-60

Contact Information for Business Card

As listed in project description

Font styles to use
Serif

Requirements
Must have
• Large logo on back of card

```html
<!DOCTYPE html>
<html lang="en">
<head>
<meta charset="utf-8">
<title>Tovrin business card</title>
<link rel="stylesheet" href="https://fonts.googleapis.com/css2?family=Arimo:wght@400;700&display=swap">
<style>
  :root {
    --bg: #e4e4e4;
    --paper: #ffffff;
    --brand-blue: #0753a1;
    --accent-blue: #2fa3d9;
    --text-grey: #6e6e6e;
    --card-black: #2c2c2e;
    --emboss: #1c1c1d;
  }
  * { margin: 0; padding: 0; box-sizing: border-box; }
  html, body { width: 1200px; height: 802px; overflow: hidden; background: var(--bg); }
  body { position: relative; font-family: "Arimo", Arial, sans-serif; }

  .card {
    position: absolute;
    top: 236px;
    width: 540px;
    height: 330px;
    overflow: hidden;
  }
  .card--front { left: 40px; background: var(--paper); }
  .card--back { left: 620px; background: var(--card-black); }

  .front-band { position: absolute; inset: 0; }

  .wordmark {
    position: absolute;
    font-weight: 700;
    letter-spacing: 1px;
    line-height: 1;
  }
  .card--front .wordmark { left: 36px; top: 58px; font-size: 54px; color: var(--brand-blue); }
  .card--back .wordmark {
    left: 0; right: 0; top: 128px; text-align: center;
    font-size: 78px; color: var(--emboss);
  }

  .person { position: absolute; left: 36px; top: 136px; }
  .person__name { font-size: 21px; color: var(--accent-blue); text-transform: uppercase; line-height: 1.1; }
  .person__role { font-size: 15px; color: var(--text-grey); margin-top: 3px; }

  .address { position: absolute; left: 36px; top: 194px; font-size: 14px; color: var(--text-grey); line-height: 1.35; font-style: normal; }

  .contacts { position: absolute; left: 36px; top: 246px; list-style: none; font-size: 14px; color: var(--text-grey); }
  .contacts li { display: flex; align-items: center; gap: 8px; line-height: 1.45; }
  .contacts svg { width: 12px; height: 12px; flex: none; }
</style>
</head>
<body>
  <section class="card card--front" aria-label="Business card front">
    <svg class="front-band" viewBox="0 0 540 330" aria-hidden="true">
      <polygon points="300,0 420,0 540,250 540,330 420,330" fill="var(--brand-blue)"/>
    </svg>
    <div class="wordmark">TOVRIN</div>
    <div class="person">
      <p class="person__name">Warren Halbeck</p>
      <p class="person__role">General Manager</p>
    </div>
    <address class="address">87 Marrow Ave<br>Pendlebay, QLD, 4023</address>
    <ul class="contacts">
      <li>
        <svg viewBox="0 0 12 12"><path d="M3 1l2 2.5-1.2 1.2a6 6 0 0 0 3.5 3.5L8.5 7 11 9l-1.5 2C5 11 1 7 1 2.5z" fill="var(--accent-blue)"/></svg>
        0472 915 348
      </li>
      <li>
        <svg viewBox="0 0 12 12"><rect x="1" y="2.5" width="10" height="7" fill="none" stroke="var(--accent-blue)" stroke-width="1.2"/><path d="M1 2.5l5 4 5-4" fill="none" stroke="var(--accent-blue)" stroke-width="1.2"/></svg>
        Warren.halbeck@tovrin.com.au
      </li>
      <li>
        <svg viewBox="0 0 12 12"><circle cx="6" cy="6" r="5" fill="none" stroke="var(--accent-blue)" stroke-width="1.2"/><path d="M1 6h10M6 1c-2.5 3-2.5 7 0 10M6 1c2.5 3 2.5 7 0 10" fill="none" stroke="var(--accent-blue)" stroke-width="1"/></svg>
        www.tovrin.com.au
      </li>
    </ul>
  </section>

  <section class="card card--back" aria-label="Business card back">
    <div class="wordmark">TOVRIN</div>
  </section>
</body>
</html>
```